Visitenkarte für Ergotherapiepraxis
Zielgruppe
Wir arbeiten mit Kindern und Erwachsene jeden Alters.
Diese Personen kommen mit Beeinträchtigungen (körperlich, seelisch, schulisch) im täglichen Leben zu uns. Wir unterstützen unsere Patienten die Beeinträchtigungen zu verringern oder zu kompensieren und so den Alltag besser bewältigen zu können.
Aufgabenstellung
Ein Design was Kinder und Erwachsene anspricht, aber nicht zu verspielt wirkt. Es soll vertrauenserweckend sein. Eventuell sollte die Visitenkarte ein "aufgehendes oder erblühendes oder aufsteigendes" Element enthalten (=zu Beginn war die Beeinträchtigung dann steigt die Lebensqualität als Folge der Behandlung)
Daten vorn:
Ergotherapiepraxis

```html
<!DOCTYPE html>
<html lang="de">
<head>
<meta charset="utf-8">
<title>Visitenkarte Ergotherapiepraxis</title>
<link rel="stylesheet" href="https://fonts.googleapis.com/css2?family=Arimo:wght@400;700&display=swap">
<style>
  :root {
    --backdrop: #e6e1da;
    --card: #ffffff;
    --green: #5e9a3a;
    --red: #d8434b;
    --red-deep: #b3222d;
    --grey: #b4b4b4;
  }
  * { margin: 0; padding: 0; box-sizing: border-box; }
  html, body { width: 1200px; height: 751px; overflow: hidden; background: var(--backdrop); }
  body { position: relative; font-family: "Arimo", Arial, sans-serif; }
  .card {
    position: absolute;
    top: 214px;
    width: 500px;
    height: 324px;
    background: var(--card);
    box-shadow: 0 6px 18px rgba(0,0,0,0.12);
    overflow: hidden;
  }
  .card--back { left: 60px; }
  .card--front { left: 640px; }
  .card__swoosh { position: absolute; inset: 0; width: 100%; height: 100%; }
  .back__role {
    position: absolute; left: 56px; top: 128px;
    color: var(--green); font-size: 25px; font-weight: 400; letter-spacing: 0.3px;
  }
  .front__brand {
    position: absolute; left: 30px; top: 96px;
    display: flex; align-items: center; gap: 8px;
    color: var(--green); font-size: 15px; font-weight: 700;
  }
  .front__brand-dot { width: 14px; height: 14px; border-radius: 50%; background: var(--green); }
  .front__name {
    position: absolute; left: 180px; top: 44px;
    color: var(--green); font-size: 25px; font-weight: 700; line-height: 1.1;
  }
  .front__phone {
    position: absolute; left: 40px; top: 168px;
    font-size: 25px; font-weight: 400;
  }
  .front__phone-label { color: var(--grey); }
  .front__phone-number { color: var(--red); }
  .front__address {
    position: absolute; left: 40px; bottom: 26px;
    color: #ffffff; font-size: 16px; letter-spacing: 0.3px;
  }
</style>
</head>
<body>
  <section class="card card--back">
    <svg class="card__swoosh" viewBox="0 0 500 324" aria-hidden="true">
      <defs>
        <linearGradient id="band-back" x1="0" y1="1" x2="1" y2="0">
          <stop offset="0" stop-color="#d8434b"/>
          <stop offset="1" stop-color="#b3222d"/>
        </linearGradient>
      </defs>
      <path d="M0,250 Q290,225 420,110 Q470,60 500,40 L500,324 L0,324 Z" fill="url(#band-back)"/>
    </svg>
    <p class="back__role">Behandelnder Therapeut</p>
  </section>

  <section class="card card--front">
    <svg class="card__swoosh" viewBox="0 0 500 324" aria-hidden="true">
      <defs>
        <linearGradient id="band-front" x1="0" y1="1" x2="1" y2="0">
          <stop offset="0" stop-color="#d8434b"/>
          <stop offset="1" stop-color="#b3222d"/>
        </linearGradient>
      </defs>
      <path d="M0,255 Q300,235 425,115 Q470,70 500,38 L500,324 L0,324 Z" fill="url(#band-front)"/>
    </svg>
    <div class="front__brand"><span class="front__brand-dot"></span>Ergo Lenz</div>
    <h1 class="front__name">Ergotherapiepraxis<br>Sabine Lenz</h1>
    <p class="front__phone"><span class="front__phone-label">Telefon: </span><span class="front__phone-number">033700 48215</span></p>
    <p class="front__address">Am Lindenweg 4 &nbsp;·&nbsp; 14900 Feldbach, OT Rosenau</p>
  </section>
</body>
</html>
```